Business Card Design - Amberfield Court

We are looking at a new design for our business cards that has a modern and professional look. We run a residential aged care facility focussing on the care of residents. The cards will be used for potential clients, consultants and business opportunities in this sector. Blue and white is our main colours and would to see these colours incorporated in the design.
Industry/Entity Type
Business
Contact Information for Business Card
Amberfield Court, Darren Walsh, dwalsh@amberfieldcourt.com.au, Finance Manager, 0472 639 208, BCom, 37 Marrabel Crescent, Brindle Vale, Qld 4093.
Look and feel
Each slider illustrates characteristics of the customer's brand and the style your logo design should communicate.

```html
<!DOCTYPE html>
<html lang="en">
<head>
<meta charset="utf-8">
<title>Amberfield Court – Business Card</title>
<link rel="stylesheet" href="https://fonts.googleapis.com/css2?family=Arimo:ital,wght@0,400;0,700;1,400&display=swap">
<style>
  :root {
    --page: #e9e6e2;
    --card: #ffffff;
    --brand-blue: #4b7a8f;
    --brand-blue-deep: #3d6a80;
    --ink-dark: #2c4656;
    --ink-body: #4a4a4a;
    --tag-grey: #a2968e;
    --white: #ffffff;
  }
  * { box-sizing: border-box; margin: 0; padding: 0; }
  html, body { width: 1200px; height: 950px; overflow: hidden; }
  body {
    background: var(--page);
    font-family: "Arimo", Arial, sans-serif;
    display: flex; flex-direction: column; align-items: center; justify-content: center; gap: 40px;
  }
  .card {
    position: relative; width: 640px; height: 391px;
    background: var(--card); overflow: hidden;
    box-shadow: 0 6px 20px rgba(0,0,0,.15);
  }
  /* front */
  .brand { position: absolute; left: 48px; top: 44px; }
  .brand-name {
    font-size: 30px; font-weight: 400; letter-spacing: 3px;
    color: var(--ink-dark); text-transform: uppercase; line-height: 1;
  }
  .tagline {
    margin-top: 8px; margin-left: -10px; width: 320px; padding: 4px 10px;
    background: var(--tag-grey); color: var(--white);
    font-style: italic; font-size: 17px; letter-spacing: .5px; white-space: nowrap;
  }
  .band {
    position: absolute; left: 0; top: 150px; width: 100%; height: 54px;
    background: var(--brand-blue);
  }
  .band-drop {
    position: absolute; right: 0; top: 150px; width: 220px; height: 108px;
    background: linear-gradient(160deg, var(--brand-blue) 0%, var(--brand-blue-deep) 100%);
  }
  .people-area {
    position: absolute; right: 120px; top: 200px; width: 72px; height: 58px;
    background: linear-gradient(180deg, #7fa6b8, #b9d0da);
  }
  .person { position: absolute; left: 30px; top: 156px; color: var(--white); }
  .person-name { font-size: 23px; font-weight: 700; }
  .person-name .credential { font-size: 15px; font-weight: 700; margin-left: 4px; }
  .person-role { font-size: 14px; margin-top: 3px; }
  .contact { position: absolute; left: 30px; top: 236px; list-style: none; }
  .contact li {
    display: flex; align-items: center; gap: 10px;
    font-size: 16px; color: var(--ink-body); line-height: 22px;
  }
  .contact svg { width: 14px; height: 14px; fill: var(--brand-blue-deep); flex: none; }
  .address {
    position: absolute; right: 36px; bottom: 34px; text-align: right;
    font-style: normal; font-size: 17px; line-height: 24px; color: var(--ink-body);
  }
  /* back */
  .back-brand { position: absolute; left: 0; right: 0; top: 150px; text-align: center; }
  .back-brand .brand-name { font-size: 36px; }
  .back-brand .tagline { margin: 12px auto 0; width: 340px; }
</style>
</head>
<body>

<section class="card card-front" aria-label="Business card front">
  <div class="brand">
    <p class="brand-name">Amberfield Court</p>
    <p class="tagline">Care, Comfort, Companionship</p>
  </div>

  <div class="band"></div>
  <div class="band-drop"></div>
  <div class="people-area" role="img" aria-label="Silhouette of a carer and resident"></div>

  <div class="person">
    <p class="person-name">Darren Walsh<span class="credential">BCom</span></p>
    <p class="person-role">Finance Manager</p>
  </div>

  <ul class="contact">
    <li><svg viewBox="0 0 16 16" aria-hidden="true"><path d="M3 1h3l1.5 4-2 1.2a9 9 0 0 0 4.3 4.3L11 8.5l4 1.5v3a2 2 0 0 1-2 2A12 12 0 0 1 1 3a2 2 0 0 1 2-2z"/></svg>0472 639 208</li>
    <li><svg viewBox="0 0 16 16" aria-hidden="true"><path d="M1 3h14L8 9z"/><path d="M1 4.5l7 6 7-6V13H1z"/></svg>dwalsh@amberfieldcourt.com.au</li>
    <li><svg viewBox="0 0 16 16" aria-hidden="true"><circle cx="8" cy="8" r="7"/></svg>www.amberfieldcourt.com.au</li>
  </ul>

  <address class="address">
    37 Marrabel Crescent<br>
    Brindle Vale, Qld 4093.
  </address>
</section>

<section class="card card-back" aria-label="Business card back">
  <div class="back-brand">
    <p class="brand-name">Amberfield Court</p>
    <p class="tagline">Care, Comfort, Companionship</p>
  </div>
</section>

</body>
</html>
```